SaaS Early tech startup business card design

Unique design for experience ecommerce platform company. the business cards will be used by executive members. conformance with color code is required.

```html
<!DOCTYPE html>
<html lang="en">
<head>
<meta charset="utf-8">
<title>Kovra business card</title>
<link rel="stylesheet" href="https://fonts.googleapis.com/css2?family=Poppins:wght@400;600;800&display=swap">
<style>
  :root {
    --page: #1c1c1f;
    --card: #24233b;
    --teal: #22b89c;
    --teal-light: #4fd0ad;
    --blue: #0e6f9c;
    --white: #f4f6f8;
    --rule: #c9ccd6;
    --band: linear-gradient(90deg,
      #0b5f8f 0 16%, #0f74a1 16% 32%, #1389aa 32% 48%,
      #1a9ea9 48% 64%, #24b4a3 64% 82%, #4ccbab 82% 100%);
  }
  * { box-sizing: border-box; margin: 0; padding: 0; }
  html, body { width: 1200px; height: 900px; overflow: hidden; }
  body {
    background: var(--page);
    font-family: "Poppins", Arial, sans-serif;
    color: var(--white);
    position: relative;
  }
  .card {
    position: absolute;
    left: 250px;
    width: 700px;
    height: 400px;
    background: var(--card);
    border-radius: 22px;
    overflow: hidden;
  }
  .card--front { top: 35px; }
  .card--back { top: 465px; }
  .card__band {
    position: absolute;
    left: 0; right: 0; bottom: 0;
    height: 22px;
    background: var(--band);
  }
  .brand {
    position: absolute;
    font-weight: 800;
    color: var(--teal);
    letter-spacing: -2px;
    line-height: 1;
  }
  .card--front .brand { right: 70px; top: 40px; font-size: 78px; }
  .card--back .brand { right: 60px; top: 55px; font-size: 100px; }
  .brand-motif {
    position: absolute;
    right: 30px; top: 140px;
    width: 210px; height: 120px;
    border-radius: 40px;
    background: radial-gradient(ellipse at center, rgba(34,184,156,0.35), rgba(14,111,156,0.15) 60%, rgba(36,35,59,0) 75%);
  }
  .stat {
    position: absolute;
    left: 55px; top: 175px;
  }
  .stat__figure {
    font-size: 66px;
    font-weight: 400;
    color: var(--teal);
    line-height: 1;
  }
  .stat__text {
    margin-top: 10px;
    font-size: 22px;
    line-height: 1.3;
    color: var(--white);
  }
  .person {
    position: absolute;
    left: 50px; top: 40px;
  }
  .person__name {
    font-size: 28px;
    font-weight: 800;
    color: var(--teal);
    line-height: 1.1;
  }
  .person__role { font-size: 18px; color: var(--white); }
  .rule {
    position: absolute;
    height: 1px;
    background: var(--rule);
  }
  .rule--address { left: 320px; right: 45px; top: 195px; }
  .rule--contact { left: 45px; width: 300px; top: 262px; }
  .address {
    position: absolute;
    right: 50px; top: 208px;
    text-align: right;
    font-size: 19px;
    line-height: 1.3;
  }
  .contact {
    position: absolute;
    left: 45px; top: 274px;
    list-style: none;
  }
  .contact__item {
    display: flex;
    align-items: center;
    gap: 12px;
    font-size: 20px;
    line-height: 1;
    margin-bottom: 8px;
  }
  .contact__icon {
    width: 24px; height: 24px;
    border-radius: 6px;
    background: var(--teal);
    display: flex; align-items: center; justify-content: center;
    flex: none;
  }
</style>
</head>
<body>

<section class="card card--front">
  <div class="brand">kovra</div>
  <div class="brand-motif" role="img" aria-label="Faint decorative line motif"></div>
  <div class="stat">
    <div class="stat__figure">63%</div>
    <p class="stat__text">Of Consumer Value<br>Privacy Over Popularity<br>When Dealing With<br>Online Platform</p>
  </div>
  <div class="card__band"></div>
</section>

<section class="card card--back">
  <div class="person">
    <div class="person__name">Daniel Reyes</div>
    <div class="person__role">Manager</div>
  </div>
  <div class="brand">kovra</div>
  <div class="rule rule--address"></div>
  <p class="address">Your address, city<br>state, ZIP 0000</p>
  <div class="rule rule--contact"></div>
  <ul class="contact">
    <li class="contact__item">
      <span class="contact__icon">
        <svg width="14" height="14" viewBox="0 0 24 24"><path fill="#24233b" d="M6.6 10.8a15 15 0 0 0 6.6 6.6l2.2-2.2c.3-.3.7-.4 1-.2 1.1.4 2.3.6 3.6.6.6 0 1 .4 1 1V20c0 .6-.4 1-1 1A17 17 0 0 1 3 4c0-.6.4-1 1-1h3.5c.6 0 1 .4 1 1 0 1.3.2 2.5.6 3.6.1.3 0 .7-.2 1z"/></svg>
      </span>
      555-318-2047
    </li>
    <li class="contact__item">
      <span class="contact__icon">
        <svg width="15" height="12" viewBox="0 0 24 18"><rect x="1" y="1" width="22" height="16" rx="2" fill="none" stroke="#24233b" stroke-width="2.2"/><path d="M2 2l10 8 10-8" fill="none" stroke="#24233b" stroke-width="2.2"/></svg>
      </span>
      youremail@mailbox.com
    </li>
    <li class="contact__item">
      <span class="contact__icon">
        <svg width="15" height="15" viewBox="0 0 24 24" fill="none" stroke="#24233b" stroke-width="2"><circle cx="12" cy="12" r="10"/><path d="M2 12h20M12 2c3 3 3 17 0 20M12 2c-3 3-3 17 0 20"/></svg>
      </span>
      www.yourwebsite.com
    </li>
  </ul>
  <div class="card__band"></div>
</section>

</body>
</html>
```